Upland Bird Hunting Preserve and Pointing Dog kennel

Need Price packages outlined for the bird hunting business. List the kennel and that we provide training and dogs for sale.
The preserve is "Tall Heron Provisions" the dog kennel is "Pine Hollow Setters"
1/2 Day Upland Field Hunts: 5 Pheasants $120
7 Chukar $125
Continental Hunt 12 Pheasants $325 includes meal, minimum 12 hunters
Guides available $100

Target Market(s)

upland bird hunters

Industry/Entity Type

hunting, outdoor

Colors
EE7325
F08F49
F5BC92
FAE3D3
FDF4ED

```html
<!DOCTYPE html>
<html lang="en">
<head>
<meta charset="utf-8">
<title>Tall Heron Provisions – Upland Hunts</title>
<link href="https://fonts.googleapis.com/css2?family=Graduate&family=Poppins:wght@400;500;600;700;800&family=Oswald:wght@500;600&family=Crimson+Text&display=swap" rel="stylesheet">
<style>
  :root{
    --orange:#F29B35;
    --orange-deep:#EE7325;
    --bark:#2a0a07;
    --bark-mid:#3a120c;
    --night:#0d0302;
    --paper:#ffffff;
    --ink:#1d1d1d;
  }
  *{margin:0;padding:0;box-sizing:border-box}
  html,body{width:938px;height:1200px;overflow:hidden;background:var(--paper)}
  .flyer{position:relative;width:938px;height:1200px;overflow:hidden;font-family:"Poppins",sans-serif;color:#fff;
    background:radial-gradient(ellipse at 50% 45%,var(--bark-mid) 0%,var(--bark) 55%,var(--night) 100%)}
  .abs{position:absolute}
  .brand{left:57px;top:50px;font-family:"Graduate",serif;line-height:1}
  .brand .top{font-size:76px;color:var(--orange);letter-spacing:-1px;white-space:nowrap}
  .brand .bottom{font-size:55px;color:#fff;margin-top:6px;white-space:nowrap;letter-spacing:-0.5px}
  .locale{left:573px;top:48px}
  .locale .town{font-family:"Crimson Text",serif;font-size:38px;line-height:1}
  .locale .tag{font-size:30px;color:var(--orange);line-height:1.25;margin-top:2px}
  .art{background:linear-gradient(160deg,rgba(255,255,255,.22),rgba(255,255,255,.08));border-radius:8px}
  .hunt-label{left:57px;top:453px;font-weight:700;font-size:21px;line-height:1.3}
  .hunt-label em{font-style:normal;color:var(--orange)}
  .price-card{top:358px;width:186px}
  .price-card .name{background:#fff;color:var(--ink);font-weight:700;font-size:18px;text-align:center;height:46px;line-height:48px}
  .price-card .cost{margin-top:6px;background:var(--orange);height:94px;text-align:center;font-family:"Oswald",sans-serif;font-weight:500;font-size:62px;line-height:94px}
  .price-card .cost sup{font-size:28px;vertical-align:28px;margin-right:4px}
  .panel{top:577px;border:1px solid rgba(255,255,255,.85)}
  .panel-head{position:absolute;left:-1px;right:-1px;top:-1px;height:46px;background:var(--orange);color:var(--ink);font-weight:700;font-size:17px;line-height:46px;text-align:center}
  .tick{position:absolute;width:20px;height:16px;transform:translateX(-50%)}
  .col-text{position:absolute;text-align:center;transform:translateX(-50%);font-size:14.5px;line-height:1.2;white-space:nowrap}
  .big-num{font-weight:800;color:var(--orange);font-size:36px;line-height:1}
  .divider{position:absolute;left:147px;top:88px;width:1px;height:188px;background:rgba(255,255,255,.5)}
  .days{position:absolute;transform:translateX(-50%);width:81px;text-align:center}
  .days .head{font-weight:800;color:var(--orange);font-size:30px;line-height:1;display:flex;justify-content:center;align-items:center;gap:3px}
  .days .head span{font-size:12.5px;color:#fff;line-height:1;text-align:left}
  .days .note{background:#fff;color:var(--ink);font-size:6px;font-weight:600;line-height:1.1;padding:3px 0;margin-top:5px}
  .days .fee{background:var(--orange);color:var(--ink);font-family:"Oswald",sans-serif;font-size:26px;line-height:40px}
  .days .fee sup{font-size:12px;vertical-align:12px}
  .deer{position:absolute;left:275px;top:107px;width:128px;transform:translateX(-50%);text-align:center;white-space:nowrap}
  .deer .small{font-weight:700;color:var(--orange);font-size:10.5px;line-height:1.2}
  .deer .large{font-weight:700;font-size:23px;line-height:1.1;margin-top:8px}
  .contact{left:518px;top:818px}
  .contact .who{font-weight:700;font-size:22px}
  .contact .phone{display:flex;align-items:center;gap:8px;font-weight:700;font-size:29px;color:var(--orange);margin-top:2px}
  .paper{left:0;top:0;width:938px;height:1200px}
  .perks{left:57px;top:1006px;color:var(--ink);font-weight:700;font-size:20px;line-height:1.35}
  .perks li{list-style:none;position:relative;padding-left:33px;margin-bottom:22px}
  .perks svg{position:absolute;left:0;top:5px}
  .kennel{left:410px;top:1030px;width:230px;text-align:center;color:var(--ink)}
  .kennel .name{font-weight:600;font-size:24px;line-height:1.15}
  .kennel .rule{height:3px;background:var(--ink);margin:12px 6px 8px}
  .kennel .town{font-family:"Crimson Text",serif;font-size:20px;letter-spacing:1px}
  .house{left:700px;top:1040px;width:190px;text-align:center;color:var(--ink)}
  .house .dot{width:22px;height:22px;border-radius:50%;background:var(--ink);margin:0 auto 10px}
  .house .name{font-weight:600;font-size:21px;line-height:1.15}
</style>
</head>
<body>
<div class="flyer">
  <div class="abs art" role="img" aria-label="Dark field grass silhouettes along the lower edge" style="left:60px;top:690px;width:878px;height:220px;background:linear-gradient(180deg,rgba(120,60,50,0),rgba(110,55,45,.35));border-radius:0"></div>

  <div class="abs brand">
    <div class="top">TALL HERON</div>
    <div class="bottom">PROVISIONS LLC</div>
  </div>
  <div class="abs locale">
    <div class="town">Millbrook, MO</div>
    <div class="tag">Licensed Shooting<br>Preserve</div>
  </div>

  <div class="abs art" role="img" aria-label="Flushing pheasants in flight, white silhouettes" style="left:105px;top:220px;width:112px;height:60px"></div>
  <div class="abs art" role="img" aria-label="White silhouettes of a pointing dog and a kneeling hunter aiming a shotgun" style="left:395px;top:190px;width:490px;height:166px"></div>
  <div class="abs art" role="img" aria-label="Round upland hunting badge with hunter and birds" style="left:73px;top:307px;width:140px;height:130px;border-radius:50%"></div>

  <div class="abs hunt-label">UPLAND FIELD<br>HUNTS – <em>½ DAY</em></div>

  <div class="abs price-card" style="left:296px"><div class="name">5 PHEASANTS</div><div class="cost"><sup>$</sup>120</div></div>
  <div class="abs price-card" style="left:495px"><div class="name">7 CHUKAR</div><div class="cost"><sup>$</sup>125</div></div>
  <div class="abs price-card" style="left:695px"><div class="name">8 QUAIL</div><div class="cost"><sup>$</sup>100</div></div>

  <section class="abs panel" style="left:57px;width:355px;height:301px">
    <div class="panel-head">CONTINENTAL PHEASANT HUNT</div>
    <svg class="tick" style="left:66px;top:80px" viewBox="0 0 20 16"><polyline points="2,8 8,14 18,2" fill="none" stroke="#F29B35" stroke-width="3"/></svg>
    <div class="col-text" style="left:66px;top:104px"><div class="big-num">12</div>Hunter<br>Minimum</div>
    <svg class="tick" style="left:66px;top:192px" viewBox="0 0 20 16"><polyline points="2,8 8,14 18,2" fill="none" stroke="#F29B35" stroke-width="3"/></svg>
    <div class="col-text" style="left:66px;top:218px">Lodging<br>availablecall<br>for pricing</div>
    <div class="divider"></div>
    <svg class="tick" style="left:253px;top:80px" viewBox="0 0 20 16"><polyline points="2,8 8,14 18,2" fill="none" stroke="#F29B35" stroke-width="3"/></svg>
    <div class="col-text" style="left:253px;top:102px">
      <div style="display:flex;align-items:center;justify-content:center;gap:4px;text-align:left"><span class="big-num"><sup style="font-size:18px">$</sup>325</span><span style="font-size:14px;line-height:1.15">Per<br>Hunter</span></div>
      <div style="margin-top:4px">Includes <span style="color:var(--orange)">12</span> Pheasants<br>per hunter &amp; meal</div>
    </div>
    <svg class="tick" style="left:253px;top:192px" viewBox="0 0 20 16"><polyline points="2,8 8,14 18,2" fill="none" stroke="#F29B35" stroke-width="3"/></svg>
    <div class="col-text" style="left:253px;top:218px">All hunts include<br>bird cleaning</div>
  </section>

  <section class="abs panel" style="left:518px;width:355px;height:228px">
    <div class="panel-head">GUIDED SPRING TURKEY HUNTS</div>
    <svg class="tick" style="left:68px;top:74px" viewBox="0 0 20 16"><polyline points="2,8 8,14 18,2" fill="none" stroke="#F29B35" stroke-width="3"/></svg>
    <svg class="tick" style="left:166px;top:74px" viewBox="0 0 20 16"><polyline points="2,8 8,14 18,2" fill="none" stroke="#F29B35" stroke-width="3"/></svg>
    <svg class="tick" style="left:275px;top:74px" viewBox="0 0 20 16"><polyline points="2,8 8,14 18,2" fill="none" stroke="#F29B35" stroke-width="3"/></svg>
    <div class="days" style="left:68px;top:98px"><div class="head">3<span>DAY<br>HUNT</span></div><div class="note">INCLUDES MEALS<br>&amp; LODGING</div><div class="fee"><sup>$</sup>1600</div></div>
    <div class="days" style="left:166px;top:98px"><div class="head">5<span>DAY<br>HUNT</span></div><div class="note">NCLUDES MEALS<br>&amp; LODGING</div><div class="fee"><sup>$</sup>2750</div></div>
    <div class="deer"><div class="small">GUIDED WHITETAIL<br>DEER HUNTS</div><div class="large">RIFLE &amp;<br>ARCHERY</div></div>
  </section>

  <div class="abs contact">
    <div class="who">DALE MORGAN</div>
    <div class="phone">
      <svg width="26" height="26" viewBox="0 0 26 26"><circle cx="13" cy="13" r="13" fill="#fff"/><path d="M9 7c1 0 2 2.5 2 3.3s-1.2 1.2-1 2c.5 1.6 2 3.1 3.7 3.7.8.2 1.2-1 2-1s3.3 1 3.3 2c0 1.3-1.6 2.3-2.7 2.3C11.2 19.3 6.7 14.8 6.7 9.7 6.7 8.6 7.700 7 9 7z" fill="#2a0a07"/></svg>
      555-014-2273
    </div>
  </div>

  <svg class="abs paper" viewBox="0 0 938 1200" aria-hidden="true">
    <polygon fill="#fff" points="0,917 20,905 45,912 70,908 95,922 120,915 150,925 180,918 215,930 250,921 290,926 330,913 370,920 410,906 450,914 490,903 530,911 570,904 610,914 650,907 690,918 730,910 770,915 810,906 850,912 890,904 920,909 938,905 938,1200 0,1200"/>
  </svg>

  <ul class="abs perks">
    <li><svg width="20" height="16" viewBox="0 0 20 16"><polyline points="2,8 8,14 18,2" fill="none" stroke="#F29B35" stroke-width="3"/></svg>We provide training<br>and dogs for sale.</li>
    <li><svg width="20" height="16" viewBox="0 0 20 16"><polyline points="2,8 8,14 18,2" fill="none" stroke="#F29B35" stroke-width="3"/></svg>Puppies and started<br>dogs available</li>
  </ul>

  <div class="abs kennel">
    <div class="name">Pine Hollow<br>Setters</div>
    <div class="rule"></div>
    <div class="town">CEDAR BEND, MO</div>
  </div>

  <div class="abs house">
    <div class="dot"></div>
    <div class="name">Tall Heron<br>Provisions</div>
  </div>
</div>
</body>
</html>
```